QP Fiduciary Website Redesign Contest

We want to refresh our website to be more insitutional, professional for an international audience. We have designed a new logo for this purpose and that has been attached. A full brand brief and positioning statement has also been attached. Please read through all the documents carefully before designing. The old website is found here: https://qp-fiduciary.example/

Target Market(s)

Actuaries and associated businesses internationally

Industry/Entity Type

professional services - actuaries

Number of Pages Required

3 page

Font styles to use
Sans Serif

Colors
0054AA
0677BA
7BADD7
CADEEF
E8F1F8
0094D4
00A9DD
6FCCEA
C7EBF8
E9F6FB
F0912C
F2A743
F7CA91
FBE8D2
FDF5EE
EE7325
F08F49
F5BC92
FAE3D3
FDF4ED
EB3D1F
EC4F4E
F09395
F8D3D4
FCEDEE

Requirements
Must have
• blues and greens to match the logo color, complimentary colors, navigation
Nice to have
• old site: https://qp-fiduciary.example/

```html
<!DOCTYPE html>
<html lang="en">
<head>
<meta charset="utf-8">
<title>QP Fiduciary — Actuarial Software</title>
<link href="https://fonts.googleapis.com/css2?family=Orbitron:wght@400;500&family=Poppins:wght@400;500;600&display=swap" rel="stylesheet">
<style>
:root{
  --blue:#0f33d4;
  --blue-deep:#0a25b8;
  --blue-bright:#1f46e6;
  --heading-blue:#1b3fd9;
  --orange:#f65a0a;
  --ink:#151515;
  --grey-line:#cfcfcf;
  --circle-fill:#f5f5fb;
  --footer:#111111;
  --white:#ffffff;
}
*{box-sizing:border-box;margin:0;padding:0}
html,body{width:1200px;height:4193px;overflow:hidden}
body{position:relative;font-family:'Poppins',sans-serif;color:var(--ink);background:var(--white)}
.abs{position:absolute}
.display{font-family:'Orbitron',sans-serif;font-weight:400;letter-spacing:1.5px;text-transform:uppercase}
.accent-blue{color:var(--heading-blue)}
.accent-orange{color:var(--orange)}
.btn{position:absolute;background:var(--orange);color:var(--ink);font-size:14px;font-weight:500;display:flex;align-items:center;justify-content:center}
.wordmark{font-family:'Poppins',sans-serif;font-weight:600;font-size:30px;letter-spacing:2px;display:flex;align-items:center;gap:12px;text-transform:uppercase}
.wordmark .dot{width:18px;height:18px;border-radius:50%;background:var(--orange)}

.site-header{left:0;top:0;width:1200px;height:111px;background:var(--white)}
.main-nav{right:147px;top:76px;display:flex;gap:22px;font-size:14px;font-weight:500}
.main-nav .active{color:var(--heading-blue)}

.band-blue{left:0;width:1200px;background:radial-gradient(ellipse at 75% 20%,var(--blue-bright),var(--blue) 55%,var(--blue-deep));overflow:hidden;color:var(--white)}
.center{left:0;width:1200px;text-align:center}

.hero-title{font-size:36px;line-height:53px}
.hero-sub{font-size:17px;line-height:26px}

.section-title{font-size:33px;line-height:52px}
.section-lead{font-size:16px;line-height:26px;color:var(--ink)}

.flow-item{left:659px;width:220px;height:62px;border-top:1px solid var(--grey-line);border-bottom:1px solid var(--grey-line);font-size:16px;display:flex;align-items:center;padding-left:22px}

.solution-icon{width:76px;height:76px;border-radius:50%;background:var(--white);border:4px solid #8fa3f2;display:flex;align-items:center;justify-content:center}
.solution-title{font-size:20px}
.solution-text{font-size:14px;line-height:27px;width:260px}

.tl-text{font-size:14px;line-height:27px}
.tl-dot{width:14px;height:14px;border-radius:50%;background:#8a8a8a;left:577px}

.articles{left:0;top:2919px;width:1200px;height:635px;background:linear-gradient(135deg,#dfe3f5,#eef0fa 60%,#e3e7f7)}
.article-media{height:189px;width:290px}
.article-title{font-size:20px;line-height:31px;width:300px}

.site-footer{left:0;top:3915px;width:1200px;height:278px;background:var(--footer);color:var(--white)}
.footer-nav{display:flex;gap:22px;font-size:14px;font-weight:500}
</style>
</head>
<body>

<header class="abs site-header">
  <div class="abs wordmark" style="left:143px;top:30px;color:var(--ink)"><span class="dot"></span>QP Fiduciary</div>
  <div class="btn" style="left:785px;top:21px;width:268px;height:38px">Request Technical Walkthrough</div>
  <nav class="abs main-nav">
    <span class="active">Home</span><span>Platform</span><span>Solutions</span><span>Insights</span><span>Company</span><span>Contact Us</span>
  </nav>
</header>

<section class="abs band-blue" style="top:111px;height:589px">
  <h1 class="abs center display hero-title" style="top:127px">Actuarial Software<br>For Structured, Auditable<br><span class="accent-orange">Financial Analysis</span></h1>
  <p class="abs center hero-sub" style="top:324px">Software that translates actuarial methodologies into disciplined decision-ready<br>analytical tools across diverse regulatory environments</p>
  <div class="btn" style="left:466px;top:421px;width:268px;height:41px">Request Technical Walkthrough</div>
</section>

<h2 class="abs center display section-title" style="top:788px"><span class="accent-blue">A Comprehensive</span><br>Actuarial Software Platform</h2>
<p class="abs center section-lead" style="top:923px">QP Fiduciary develops modular actuarial software designed to support reserving, valuation,<br>pricing, and risk analysis across diverse regulatory environments.</p>

<svg class="abs" style="left:0;top:1000px" width="1200" height="420" viewBox="0 1000 1200 420" fill="none">
  <circle cx="399" cy="1215" r="174" stroke="#d6d6d6" stroke-width="2"/>
  <circle cx="399" cy="1215" r="158" fill="#f5f5fb"/>
  <line x1="573" y1="1213" x2="635" y2="1213" stroke="#999" stroke-width="2"/>
  <path d="M659 1091 H645 Q635 1091 635 1101 V1325 Q635 1335 645 1335 H659 M635 1172 H659 M635 1254 H659" stroke="#999" stroke-width="2"/>
  <circle cx="573" cy="1213" r="5" fill="#888"/>
  <circle cx="661" cy="1091" r="5" fill="#888"/><circle cx="661" cy="1172" r="5" fill="#888"/>
  <circle cx="661" cy="1254" r="5" fill="#888"/><circle cx="661" cy="1335" r="5" fill="#888"/>
</svg>
<div class="abs wordmark" style="left:275px;top:1192px;font-size:27px;color:var(--ink)"><span class="dot"></span>QP Fiduciary</div>
<div class="abs flow-item" style="top:1060px">Data Inputs</div>
<div class="abs flow-item" style="top:1141px">Analysis</div>
<div class="abs flow-item" style="top:1223px">Review &amp; Governance</div>
<div class="abs flow-item" style="top:1304px">Auditable Outputs</div>

<section class="abs band-blue" style="top:1503px;height:557px">
  <h2 class="abs center display section-title" style="top:104px">Our Core Solutions</h2>

  <div class="abs solution-icon" style="left:152px;top:214px">
    <svg width="34" height="34" viewBox="0 0 34 34" fill="none" stroke="var(--blue)" stroke-width="2"><path d="M4 30 H30 M8 30 V20 M14 30 V14 M20 30 V18 M26 30 V10"/></svg>
  </div>
  <div class="abs solution-title" style="left:151px;top:318px">Reserving &amp; Valuation</div>
  <p class="abs solution-text" style="left:153px;top:362px">Software supporting structured reserving workflows and financial reporting across jurisdictions.</p>

  <div class="abs solution-icon" style="left:493px;top:214px">
    <svg width="38" height="38" viewBox="0 0 38 38" fill="none" stroke="var(--blue)" stroke-width="2"><circle cx="19" cy="19" r="16"/><circle cx="19" cy="19" r="11"/><path d="M23 14 Q19 11 16 14 Q15 18 19 19 Q23 20 22 24 Q19 27 15 24 M19 10 V28"/></svg>
  </div>
  <div class="abs solution-title" style="left:492px;top:318px">Pricing</div>
  <p class="abs solution-text" style="left:494px;top:362px">Software supporting structured reserving workflows and financial reporting across jurisdictions.</p>

  <div class="abs solution-icon" style="left:796px;top:214px">
    <svg width="36" height="36" viewBox="0 0 36 36" fill="none" stroke="var(--blue)" stroke-width="2"><circle cx="15" cy="15" r="11"/><path d="M23 23 L32 32 M15 8 L21 19 H9 Z M15 12 V15"/></svg>
  </div>
  <div class="abs solution-title" style="left:794px;top:318px">Enterprise Risk Management</div>
  <p class="abs solution-text" style="left:796px;top:362px">Software supporting structured reserving workflows and financial reporting across jurisdictions.</p>
</section>

<h2 class="abs center display section-title" style="top:2147px"><span class="accent-blue">Platform</span> Characteristics</h2>
<p class="abs center section-lead" style="top:2225px">QP Fiduciary’s platform is designed to support disciplined actuarial analysis through<br>structured workflows, transparent methodologies, and governance-ready outputs suitable<br>for institutional environments.</p>
<div class="abs" style="left:583px;top:2344px;width:2px;height:459px;background:#bdbdbd"></div>
<div class="abs tl-dot" style="top:2419px;background:var(--heading-blue)"></div>
<div class="abs tl-dot" style="top:2505px"></div>
<div class="abs tl-dot" style="top:2590px"></div>
<div class="abs tl-dot" style="top:2676px"></div>
<p class="abs tl-text" style="left:615px;top:2412px;color:var(--heading-blue)">Structured workflows suitable for<br>multi-jurisdictional review</p>
<p class="abs tl-text" style="right:649px;top:2498px;text-align:right">Transparent assumptions and<br>methodological clarity</p>
<p class="abs tl-text" style="left:615px;top:2583px">Comparative scenario analysis</p>
<p class="abs tl-text" style="right:649px;top:2669px;text-align:right">Supports professional judgment rather<br>than replacing it</p>

<section class="abs articles">
  <h2 class="abs center display section-title" style="top:96px"><span class="accent-blue">Recent</span> Articles</h2>
  <div class="abs article-media" role="img" aria-label="Abstract blue light streaks over data" style="left:133px;top:190px;background:linear-gradient(160deg,#0a1a3a,#1d5fb8 45%,#06122b)"></div>
  <div class="abs article-media" role="img" aria-label="Glowing financial bar chart in dark blue" style="left:456px;top:190px;background:radial-gradient(ellipse at 60% 60%,#1f6fb0,#071a33 70%)"></div>
  <div class="abs article-media" role="img" aria-label="Digital compliance document with governance icons" style="left:778px;top:190px;background:radial-gradient(ellipse at 50% 45%,#2aa0e8,#0b3d7a 45%,#061a3d)"></div>
  <p class="abs article-title" style="left:131px;top:402px">Methodological perspectives<br>in actuarial reserving</p>
  <p class="abs article-title" style="left:453px;top:402px">Governance considerations<br>in multi-jurisdictional analysis</p>
  <p class="abs article-title" style="left:775px;top:402px">Observations on actuarial<br>practice in emerging markets</p>
  <div class="btn" style="left:133px;top:483px;width:160px;height:40px">Read Insights</div>
  <div class="btn" style="left:455px;top:483px;width:160px;height:40px">Read Insights</div>
  <div class="btn" style="left:776px;top:483px;width:160px;height:40px">Read Insights</div>
</section>

<section class="abs band-blue" style="top:3554px;height:361px">
  <h2 class="abs center display section-title" style="top:81px">Interested In<br>Exploring The Platform?</h2>
  <div class="btn" style="left:466px;top:223px;width:268px;height:41px">Request Technical Walkthrough</div>
</section>

<footer class="abs site-footer">
  <div class="abs wordmark" style="left:151px;top:101px;color:var(--white)"><span class="dot"></span>QP Fiduciary</div>
  <nav class="abs footer-nav" style="left:554px;top:111px"><span>Company</span><span>Platform</span><span>Solutions</span><span>Insights</span><span>Contact</span></nav>
  <div class="abs" role="img" aria-label="Social profile link" style="left:1033px;top:111px;width:20px;height:20px;border-radius:3px;background:var(--white)"></div>
  <p class="abs" style="left:155px;top:166px;font-size:13px">Legal &amp; Copyright @2026.All Rights Reservd.</p>
</footer>

</body>
</html>
```